Flat bootstrap design for existing site

I'm looking for a modern flat design based around an existing logo. This has to be a custom design (no external templates), and implemented into a bootstrap framework.

The logo is attached as 2 versions - choose whichever you want, that flows better with whatever design you choose.

Added screenshots of the existing site (currently using the default bootstrap layouts). Please make your designs around those pages in the screenshots (i.e. the homepage only has the postal code input and the header). The active page has 3 screenshots, because I wanted to illustrate the other states that would be visible (in the table rows).

This is a moving/junk removal website, just for some context.

Here's some example websites (flat designs) that I like, just to give you an idea of what I'm after.

https://www.plimvora.com/
https://dacklow.com/
https://trevanu.com/
https://quobrintal.com/en/

Coding

Coded - Design and coding required

Number of Pages Required

5+ page

Colors

Designer to choose colors to be used in the design.

Requirements
Must have
• It must be a modern/simple flat design, that is built around the existing logo (attached).
• It has to be implemented using bootstrap.

```html
<!DOCTYPE html>
<html lang="en">
<head>
<meta charset="utf-8">
<title>Haulvex – Booking Details</title>
<link rel="stylesheet" href="https://fonts.googleapis.com/css2?family=Open+Sans:wght@400;600;700&display=swap">
<style>
:root{
  --sky:#4bc8f4;
  --navy:#2767a3;
  --page:#f6f6f6;
  --white:#ffffff;
  --line:#e2e2e2;
  --text:#555555;
  --heading:#3a3a3a;
  --badge:#3b3d40;
}
*{box-sizing:border-box;margin:0;padding:0}
html,body{width:1200px;height:902px;overflow:hidden}
body{font-family:"Open Sans",Arial,sans-serif;background:var(--page);color:var(--text);position:relative}
.site-header{position:absolute;left:0;top:0;width:1200px;height:88px;background:var(--white);border-top:3px solid var(--sky);border-bottom:1px solid var(--line)}
.brand{position:absolute;left:131px;top:22px;display:flex;align-items:center;gap:8px;color:var(--sky);font-weight:700;font-size:30px;letter-spacing:1px}
.brand-dot{width:16px;height:16px;border-radius:50%;background:var(--sky)}
.main-nav a{position:absolute;top:0;height:85px;line-height:85px;font-size:14px;color:#555;text-decoration:none}
.nav-book{left:494px}
.nav-how{left:603px}
.nav-driver{left:737px;width:173px;text-align:center;background:var(--sky);color:var(--white)!important}
.nav-user{left:935px}
.nav-user svg{margin-left:6px;vertical-align:middle}
.booking-panel{position:absolute;left:132px;top:121px;width:936px;height:331px;background:var(--white);border:1px solid var(--line)}
.panel-title{height:51px;background:var(--sky);color:var(--white);font-size:16px;font-weight:600;line-height:51px;padding-left:27px;margin:-1px -1px 0}
.field-label{position:absolute;font-size:13.5px;font-weight:600;color:var(--heading)}
.field{position:absolute;height:39px;border:1px solid var(--line);font-size:11.5px;line-height:37px;padding-left:11px;color:#666;background:var(--white)}
.select-arrows{position:absolute;right:10px;top:14px}
.cal-btn{position:absolute;right:-1px;top:-1px;width:42px;height:39px;background:#cfcfcf;display:flex;align-items:center;justify-content:center}
.textarea{height:71px;line-height:normal;padding-top:12px}
.btn-update{position:absolute;left:27px;top:264px;width:87px;height:38px;background:var(--sky);color:var(--white);font-size:13px;font-weight:600;text-align:center;line-height:38px}
.divider{position:absolute;left:132px;top:475px;width:936px;border-top:1px solid var(--line)}
.section-title{position:absolute;left:132px;top:494px;font-size:24px;font-weight:600;color:var(--heading);letter-spacing:.3px}
.notice{position:absolute;left:132px;top:543px;width:936px;height:51px;background:var(--navy);color:var(--white);font-size:13px;font-weight:600;line-height:51px;padding-left:27px}
.drivers{position:absolute;left:132px;top:594px;width:936px;border-collapse:collapse;background:var(--white);font-size:11.5px}
.drivers th,.drivers td{border:1px solid var(--line);text-align:left;vertical-align:middle}
.drivers th{height:49px;font-size:13.5px;font-weight:600;color:var(--heading);padding-left:27px}
.drivers td{height:40px;padding-left:26px;color:#666}
.drivers th:nth-child(2),.drivers th:nth-child(3){padding-left:15px}
.drivers td:nth-child(2){padding-left:15px}
.drivers td:nth-child(3){padding-left:18px}
.drivers td:nth-child(5){padding-left:21px}
.badge{display:inline-block;width:69px;height:24px;line-height:24px;text-align:center;background:var(--badge);color:var(--white);font-size:11px;font-weight:700;border-radius:2px}
.site-footer{position:absolute;left:0;top:846px;width:1200px;height:56px;background:var(--white);border-top:1px solid var(--line);text-align:center;font-size:11.5px;color:#666;line-height:55px}
</style>
</head>
<body>
<header class="site-header">
  <div class="brand"><span class="brand-dot"></span>HAULVEX</div>
  <nav class="main-nav">
    <a class="nav-book" href="#">BOOK</a>
    <a class="nav-how" href="#">HOW IT WORKS</a>
    <a class="nav-driver" href="#">BECOME A DRIVER</a>
    <a class="nav-user" href="#">George@mailvaro.com<svg width="8" height="5" viewBox="0 0 8 5"><path d="M0 0h8L4 5z" fill="#555"/></svg></a>
  </nav>
</header>

<section class="booking-panel">
  <div class="panel-title">BOOKING DETAILS</div>
  <div class="field-label" style="left:27px;top:68px">Package Selected :</div>
  <div class="field" style="left:26px;top:97px;width:429px">Package 1
    <svg class="select-arrows" width="7" height="10" viewBox="0 0 7 10"><path d="M0 4h7L3.5 0zM0 6h7L3.5 10z" fill="#555"/></svg>
  </div>
  <div class="field-label" style="left:479px;top:68px">Pick - up Time Selected :</div>
  <div class="field" style="left:478px;top:97px;width:429px">July 18 at 4:13 am
    <span class="cal-btn"><svg width="11" height="11" viewBox="0 0 11 11"><rect x="0.5" y="1.5" width="10" height="9" fill="none" stroke="#fff"/><path d="M0.5 4h10M3 0v3M8 0v3M3 6h1M5 6h1M7 6h1M3 8h1M5 8h1M7 8h1" stroke="#fff"/></svg></span>
  </div>
  <div class="field-label" style="left:27px;top:148px">Description</div>
  <div class="field textarea" style="left:26px;top:177px;width:881px">1 Large Stove</div>
  <div class="btn-update">UPDATE</div>
</section>

<div class="divider"></div>
<h2 class="section-title">Drivers In Your Area</h2>
<div class="notice">Please Stay on this page and be patient,while we contact the drivers and find you one ASAP</div>

<table class="drivers">
  <colgroup><col style="width:203px"><col style="width:176px"><col style="width:176px"><col style="width:176px"><col style="width:205px"></colgroup>
  <thead><tr><th>Name</th><th>Distance (km)</th><th>Agreed Pick-up time</th><th></th><th></th></tr></thead>
  <tbody>
    <tr><td>Dale Marsh</td><td>4.04km away</td><td>-</td><td></td><td><span class="badge">Pending</span></td></tr>
    <tr><td>Owen Pryce</td><td>5.7km away</td><td>-</td><td></td><td><span class="badge">Pending</span></td></tr>
    <tr><td>Milo Varga</td><td>11.13km away</td><td>-</td><td></td><td><span class="badge">Pending</span></td></tr>
    <tr><td>Reid Calloway</td><td>11.91km away</td><td>-</td><td></td><td><span class="badge">Pending</span></td></tr>
  </tbody>
</table>

<footer class="site-footer">Copyrights © Haulvex . 2017 | All rights reserved.</footer>
</body>
</html>
```